SaaS Early tech startup business card design

Unique design for experience ecommerce platform company. the business cards will be used by executive members. conformance with color code is required.

```html
<!DOCTYPE html>
<html lang="en">
<head>
<meta charset="utf-8">
<title>novra — business card</title>
<link href="https://fonts.googleapis.com/css2?family=Roboto:wght@400;500;700;900&display=swap" rel="stylesheet">
<style>
  :root {
    --backdrop: #6b6868;
    --navy: #1f2239;
    --paper: #f4f4f4;
    --brand-teal: #1a8f96;
    --deep-teal: #155863;
    --bright-teal: #13b5a0;
    --ink: #2b2f33;
    --white: #ffffff;
  }
  * { box-sizing: border-box; margin: 0; padding: 0; }
  html, body { width: 1200px; height: 1200px; overflow: hidden; }
  body {
    background: var(--backdrop);
    font-family: "Roboto", Arial, sans-serif;
    position: relative;
  }
  .card {
    position: absolute;
    width: 594px;
    height: 350px;
    border-radius: 20px;
    overflow: hidden;
  }
  .card--front { left: 299px; top: 198px; background: var(--navy); }
  .card--back { left: 292px; top: 637px; background: var(--paper); }

  .wordmark {
    font-family: "Roboto", Arial, sans-serif;
    font-weight: 900;
    color: var(--brand-teal);
    letter-spacing: 1px;
    line-height: 1;
    position: absolute;
  }
  .card--front .wordmark {
    font-size: 92px;
    left: 0; right: 0; top: 112px;
    text-align: center;
  }
  .tagline-spaced {
    position: absolute;
    left: 0; right: 0; top: 205px;
    text-align: center;
    color: var(--white);
    font-size: 17px;
    letter-spacing: 7px;
    font-weight: 400;
  }
  .pattern-area {
    position: absolute;
    border-radius: 24px;
  }
  .card--front .pattern-area {
    left: 474px; top: 218px; width: 115px; height: 121px;
    background: radial-gradient(circle at 50% 50%, rgba(26,143,150,0.45), rgba(26,143,150,0) 70%);
  }
  .card--back .pattern-area {
    left: 420px; top: 0; width: 174px; height: 210px;
    background: radial-gradient(circle at 55% 45%, rgba(90,170,180,0.35), rgba(90,170,180,0) 70%);
  }

  .card--back .wordmark {
    font-size: 86px;
    left: 36px; top: 44px;
  }
  .holder-name {
    position: absolute; left: 38px; top: 183px;
    font-size: 23px; font-weight: 700;
    color: var(--deep-teal);
    letter-spacing: -0.3px;
  }
  .holder-role, .address {
    position: absolute; left: 38px;
    font-size: 16px; color: var(--ink);
    line-height: 22px;
  }
  .holder-role { top: 211px; }
  .address { top: 257px; }

  .contact-list {
    position: absolute; left: 355px; top: 220px;
    list-style: none;
  }
  .contact-list li {
    display: flex; align-items: center;
    height: 22px;
    font-size: 16px; color: var(--ink);
  }
  .contact-list svg { width: 14px; height: 14px; margin-right: 16px; fill: var(--deep-teal); }

  .footer-band {
    position: absolute; left: 0; bottom: 0;
    width: 594px; height: 44px;
  }
  .footer-tagline {
    position: absolute; left: 300px; right: 60px; bottom: 12px;
    text-align: center;
    color: var(--white); font-size: 16px;
  }
</style>
</head>
<body>

<section class="card card--front" aria-label="Card front">
  <div class="wordmark">novra</div>
  <div class="tagline-spaced">MADE AROUND YOU</div>
  <div class="pattern-area" role="img" aria-label="Faint brand pattern decoration"></div>
</section>

<section class="card card--back" aria-label="Card back">
  <div class="pattern-area" role="img" aria-label="Faint brand pattern decoration"></div>
  <div class="wordmark">novra</div>

  <h1 class="holder-name">Karim D.</h1>
  <p class="holder-role">CTO/Owner</p>
  <p class="address">Meridian Tower, Dubai<br>Dubai Tech District, UAE</p>

  <ul class="contact-list">
    <li>
      <svg viewBox="0 0 16 16" aria-hidden="true"><path d="M2 5c0-2 3-3 6-3s6 1 6 3v1h-3V5H5v1H2z M4 7h8l2 6H2z M8 8.5a2 2 0 1 0 0 4a2 2 0 0 0 0-4z"/></svg>
      (00) 0111 NOVRA
    </li>
    <li>
      <svg viewBox="0 0 16 16" aria-hidden="true"><path d="M1 3h14v10H1z M2 4l6 5 6-5" stroke="#f4f4f4" stroke-width="1.2"/></svg>
      info@novra.net
    </li>
    <li>
      <svg viewBox="0 0 16 16" aria-hidden="true"><circle cx="8" cy="8" r="7"/><path d="M1 8h14M8 1v14M3 4h10M3 12h10" stroke="#f4f4f4" stroke-width="1" fill="none"/><ellipse cx="8" cy="8" rx="3" ry="7" stroke="#f4f4f4" stroke-width="1" fill="none"/></svg>
      www.novra.net
    </li>
  </ul>

  <svg class="footer-band" viewBox="0 0 594 44" aria-hidden="true">
    <rect x="0" y="30" width="290" height="14" fill="var(--bright-teal)"/>
    <path d="M298 0 H594 V44 H276 Z" fill="var(--deep-teal)"/>
  </svg>
  <p class="footer-tagline">Made Around You</p>
</section>

</body>
</html>
```